military training website velmotrail.com

I have a website that someone designed I am not happy with. It looks like the designer did not have the artistic ability to make a quality product. the power points are ideas that I had for the website. the business proposal was designed by someone else, and I like the style and font used, the website should reflect this document. The main part of the website should be informational with few pictures, maybe some background images behind or off to the side of the text. I would like to include a generic map with four locations marked, which, when you hover the cursor over them, show a picture of the actual location with an artistic effect or blurred so it doesn't look like a plivora atlas snip, and a picture that resembles what services are offered there, along with the text description, pictures can be found in the documents I attached, also can be stock images. this is outlined in the power points roughly.
Want to have the side menu of the major topics, or at the top, and scroll down a single page to find all of the information we have to offer

Target Market(s)

Special operations military

Industry/Entity Type

military

Coding

Coded - Design and coding required

Number of Pages Required

1 page

Other font styles liked:
• Agency FB

Colors
0054AA
0677BA
7BADD7
CADEEF
E8F1F8
00AB8E
00BBA5
67D7C9
C6EFE9
E9F9F6

Requirements
Must have
• interactive "map"
Nice to have
• professional design features to make it look like a professional website, not a beginner designer

```html
<!DOCTYPE html>
<html lang="en">
<head>
<meta charset="utf-8">
<title>Velmotrail – Master The Mission</title>
<link href="https://fonts.googleapis.com/css2?family=Roboto:wght@400;500;700&display=swap" rel="stylesheet">
<style>
:root{
  --navy:#0d1a3a;
  --steel:#4f7fb5;
  --field:#5382b8;
  --ice:#e6eef7;
  --ice-deep:#d6e3f1;
  --ink:#333a45;
  --white:#ffffff;
  --topline:#3f6fa8;
}
*{box-sizing:border-box;margin:0;padding:0}
html,body{width:1200px;height:4335px;overflow:hidden}
body{font-family:'Roboto',sans-serif;color:var(--ink);background:var(--white);position:relative}
.page{position:relative;width:1200px;height:4335px}
.abs{position:absolute}

/* header */
.topline{top:0;left:0;width:1200px;height:5px;background:var(--topline)}
.site-header{top:5px;left:0;width:1200px;height:106px;background:var(--white)}
.main-nav a{position:absolute;top:44px;font-size:15px;color:#222;text-decoration:none}
.brand-disc{left:111px;top:5px;width:310px;height:310px;border-radius:50%;background:var(--white);z-index:3;display:flex;align-items:center;justify-content:center}
.brand-name{font-weight:700;font-size:34px;color:var(--navy);letter-spacing:1px}

/* hero */
.hero{top:111px;left:0;width:1200px;height:600px;background:linear-gradient(160deg,#6f7f5a 0%,#56663f 35%,#7d8874 55%,#4b5538 80%,#3b4230 100%)}
.hero-title{left:556px;top:296px;font-size:70px;font-weight:700;color:var(--white);letter-spacing:1px}
.hero-sub{left:564px;top:388px;font-size:43px;font-weight:500;color:var(--white)}
.btn-light{left:565px;top:472px;width:155px;height:37px;border-radius:19px;background:var(--white);color:#111;font-size:14px;font-weight:500;display:flex;align-items:center;justify-content:center;text-decoration:none}

/* section titles */
.section-title{left:0;width:1200px;text-align:center;font-size:42px;font-weight:700;color:var(--navy)}
.lead{font-size:20.5px;line-height:30px;text-align:center;color:var(--ink)}

/* provide */
.provide{top:711px;left:0;width:1200px;height:823px;background:linear-gradient(180deg,var(--ice) 0%,#edf2f8 50%,var(--ice-deep) 100%)}
.feature{width:290px;text-align:center}
.feature-num{width:86px;height:86px;border-radius:50%;background:var(--steel);color:var(--white);font-size:33px;font-weight:500;display:flex;align-items:center;justify-content:center;margin:0 auto}
.feature h3{margin-top:30px;font-size:20px;font-weight:700;color:var(--navy)}
.feature p{margin-top:14px;font-size:15.5px;line-height:25.7px;color:#444}
.arrow{width:38px;height:38px}

/* mission */
.mission-photo{left:115px;top:1621px;width:420px;height:420px;border-radius:50%;border:7px solid var(--steel);background:radial-gradient(circle at 50% 45%,#e4a24a 0%,#a5652b 35%,#4c3625 70%,#2a211c 100%)}
.mission-title{left:673px;top:1703px;font-size:42px;font-weight:700;color:var(--navy)}
.mission-text{left:673px;top:1789px;width:430px;font-size:20px;line-height:30px;color:var(--ink)}

/* map */
.range-map{top:2131px;left:0;width:1200px;height:674px;background:radial-gradient(ellipse at 52% 55%,#c9b48c 0%,#a8906a 40%,#7d6a4d 75%,#5e5242 100%)}

/* qualifications */
.quals{top:2805px;left:0;width:1200px;height:390px;background:linear-gradient(180deg,#e9eff7,var(--ice-deep))}

/* contact */
.field{border:none;border-radius:30px;background:var(--field);color:var(--white);font-family:'Roboto',sans-serif;font-size:14px;padding:0 36px;outline:none}
.field::placeholder{color:var(--white)}
textarea.field{padding-top:22px;resize:none;border-radius:26px}
.btn-dark{left:513px;top:3664px;width:172px;height:37px;border-radius:19px;background:var(--navy);color:var(--white);border:none;font-family:'Roboto',sans-serif;font-size:15px}

/* gallery */
.gallery-item{top:3854px;width:308px;height:268px}

/* footer */
.site-footer{top:4213px;left:0;width:1200px;height:122px;background:var(--navy)}
.social a{position:absolute;top:41px;color:var(--white);font-size:13px;text-decoration:none;display:flex;align-items:center;gap:6px}
.social a span.dot{width:10px;height:10px;border-radius:50%;background:var(--white);display:inline-block}
.copyright{left:0;top:4307px;width:1200px;text-align:center;color:var(--white);font-size:12.5px}
</style>
</head>
<body>
<div class="page">

  <div class="abs topline"></div>
  <header class="abs site-header">
    <nav class="main-nav">
      <a href="#mission" style="left:503px">Mission</a>
      <a href="#provide" style="left:591px">What We Provide</a>
      <a href="#map" style="left:743px">Map</a>
      <a href="#quals" style="left:807px">Qualifications</a>
      <a href="#contact" style="left:943px">Contact</a>
      <a href="#gallery" style="left:1039px">Gallery</a>
    </nav>
  </header>
  <div class="abs brand-disc"><span class="brand-name">VELMOTRAIL</span></div>

  <section class="abs hero" role="img" aria-label="Operator watching a helicopter land on a green hillside"></section>
  <h1 class="abs hero-title">VELMOTRAIL</h1>
  <p class="abs hero-sub">Master The Mission</p>
  <a class="abs btn-light" href="#contact">Contact Us</a>

  <section id="provide" class="abs provide">
    <h2 class="abs section-title" style="top:77px">WHAT WE PROVIDE</h2>
    <p class="abs lead" style="left:136px;top:164px;width:928px">At Velmotrail, we draw upon years of invaluable experience gained from training at SOF facilities worldwide. Our journey has culminated in the creation of an all-encompassing training site tailored to meet the exacting needs of SOF operators. We provide a comprehensive range of training modalities meticulously crafted to enhance SOF tactics. Anchored by an unwavering commitment to realism and operational effectiveness, we ensure that your warriors are fully prepared to conquer the most demanding challenges they may face.</p>

    <div class="abs feature" style="left:102px;top:389px">
      <div class="feature-num">01</div>
      <h3>Precision Marksmanship</h3>
      <p>Utilizing Tier 1 level instructors alongside seasoned local tactical shooting experts, our comprehensive programs incorporate practice with both steel and paper targets, conducted across multiple shooting locations for varied training environments.</p>
    </div>
    <div class="abs feature" style="left:456px;top:389px">
      <div class="feature-num">02</div>
      <h3>Immersive Scenarios</h3>
      <p>We have transformed a former Soviet military stronghold into a dynamic training environment, meticulously furnished with explosives, pyrotechnics, and a live Opposition Force for verisimilar assault scenarios. Underground lays an intricate tunnel system ideal for confined-space rescue and medical training.</p>
    </div>
    <div class="abs feature" style="left:815px;top:389px">
      <div class="feature-num">03</div>
      <h3>Airfield Dominance</h3>
      <p>With a sprawling 7000ft runway available, we provide an expansive canvas for a myriad of airfield operations, including seizures, static line operations, military free fall, and helicopter insertion and extraction techniques.</p>
    </div>

    <svg class="abs arrow" style="left:52px;top:584px" viewBox="0 0 38 38" aria-label="Previous"><circle cx="19" cy="19" r="19" fill="#111"/><path d="M28 19H12M19 11l-8 8 8 8" stroke="#fff" stroke-width="4" fill="none" stroke-linecap="round" stroke-linejoin="round"/></svg>
    <svg class="abs arrow" style="left:1110px;top:584px" viewBox="0 0 38 38" aria-label="Next"><circle cx="19" cy="19" r="19" fill="#111"/><path d="M10 19h16M19 11l8 8-8 8" stroke="#fff" stroke-width="4" fill="none" stroke-linecap="round" stroke-linejoin="round"/></svg>
  </section>

  <section id="mission">
    <div class="abs mission-photo" role="img" aria-label="Team silhouettes beside tiltrotor aircraft at sunset"></div>
    <h2 class="abs mission-title">MISSION</h2>
    <p class="abs mission-text">Pioneering realistic training within a strategic theater across the full spectrum of SOF capabilities, liberating warriors from the shackles of logistical burdens and unleashing their full potential to vanquish adversaries</p>
  </section>

  <section id="map" class="abs range-map" role="img" aria-label="Stylised overhead map of the training range with four marked sites">
    <svg width="1200" height="674" viewBox="0 0 1200 674" aria-hidden="true">
      <g fill="#fff" stroke="#222" stroke-width="3">
        <g transform="translate(414,187)"><path d="M0 30C-16 10-16 0-16-6a16 16 0 0132 0c0 6 0 16-16 36z"/><circle cy="-6" r="6" fill="#222" stroke="none"/></g>
        <g transform="translate(714,160)"><path d="M0 30C-16 10-16 0-16-6a16 16 0 0132 0c0 6 0 16-16 36z"/><circle cy="-6" r="6" fill="#222" stroke="none"/></g>
        <g transform="translate(852,348)"><path d="M0 30C-16 10-16 0-16-6a16 16 0 0132 0c0 6 0 16-16 36z"/><circle cy="-6" r="6" fill="#222" stroke="none"/></g>
        <g transform="translate(534,453)"><path d="M0 30C-16 10-16 0-16-6a16 16 0 0132 0c0 6 0 16-16 36z"/><circle cy="-6" r="6" fill="#222" stroke="none"/></g>
      </g>
    </svg>
  </section>

  <section id="quals" class="abs quals">
    <h2 class="abs section-title" style="top:78px">QUALIFICATIONS SUMMARY</h2>
    <p class="abs lead" style="left:136px;top:157px;width:928px">The founders of Velmotrail OÜ bring forth a wealth of experience and expertise to the table. A former USAF Combat Controller, with nearly a decade of service in Europe; and a highly esteemed former Estonian Special Operator who graduated BUDs and Ranger School, with a proven track record of business success in Estonia. Together, we are steadfast in our dedication to delivering world-class training experiences, deeply rooted in operational excellence and strategic foresight.</p>
  </section>

  <section id="contact">
    <h2 class="abs section-title" style="top:3270px">CONTACT US</h2>
    <form>
      <input class="abs field" style="left:113px;top:3359px;width:478px;height:59px" placeholder="First Name">
      <input class="abs field" style="left:609px;top:3359px;width:478px;height:59px" placeholder="Last Name">
      <input class="abs field" style="left:113px;top:3438px;width:478px;height:58px" placeholder="Email Address">
      <input class="abs field" style="left:609px;top:3438px;width:478px;height:58px" placeholder="Phone">
      <textarea class="abs field" style="left:113px;top:3516px;width:974px;height:126px" placeholder="Message"></textarea>
      <button class="abs btn-dark" type="button">Submit</button>
    </form>
  </section>

  <section id="gallery">
    <h2 class="abs section-title" style="top:3777px">GALLERY</h2>
    <div class="abs gallery-item" style="left:111px;background:linear-gradient(180deg,#8a8478,#6b5d48 60%,#4e4232)" role="img" aria-label="Two operators with radio antennas at dusk"></div>
    <div class="abs gallery-item" style="left:444px;background:linear-gradient(160deg,#a7b1a6,#6f7f53 40%,#3e4a4f 70%,#5a5148)" role="img" aria-label="Operators on a training pad on a green hill"></div>
    <div class="abs gallery-item" style="left:778px;background:linear-gradient(180deg,#2a241c,#5a4a30 55%,#8e7a4f)" role="img" aria-label="Light vehicle beside an aircraft at night"></div>
    <svg class="abs arrow" style="left:52px;top:3973px" viewBox="0 0 38 38" aria-label="Previous"><circle cx="19" cy="19" r="19" fill="#111"/><path d="M28 19H12M19 11l-8 8 8 8" stroke="#fff" stroke-width="4" fill="none" stroke-linecap="round" stroke-linejoin="round"/></svg>
    <svg class="abs arrow" style="left:1110px;top:3973px" viewBox="0 0 38 38" aria-label="Next"><circle cx="19" cy="19" r="19" fill="#111"/><path d="M10 19h16M19 11l8 8-8 8" stroke="#fff" stroke-width="4" fill="none" stroke-linecap="round" stroke-linejoin="round"/></svg>
  </section>

  <footer class="abs site-footer">
    <div class="social">
      <a href="#" style="left:488px"><span class="dot"></span>Kestro</a>
      <a href="#" style="left:562px"><span class="dot"></span>Palvin</a>
      <a href="#" style="left:637px"><span class="dot"></span>Tevora</a>
      <a href="#" style="left:711px"><span class="dot"></span>Mirelo</a>
    </div>
  </footer>
  <p class="abs copyright">Copyright © 2024 VELMOTRAIL. All rights reserved.</p>

</div>
</body>
</html>
```